Larkmoor Drones Business Card

We are a new company based in Central Queensland, Australia that uses specalised drones (Voskel Ferra Q80) to undertake mainly agricultural operations, like spraying weeds, spraying crops, spreading seed etc. I have attached a Plimbo proof of a card I was thinking along the lines of - purely a start point. The drone used in the business card MUST be a Voskel Ferra Q80.
I am very open to other ideas, especially fonts and layout. I don't have website etc set up yet.
The images are stock and easily interchangeable, I just ask that any background images reflect the local central Queensland area. The photo of the drone is not even complete (propellers cut off) and I need a new stock photo – I’m not sure if this is an issue, or I can pay for an image if need be. PLEASE FIND AN FERRA Q80 image - 4 sprayers, not 6.
The logo/business name is very draft and looking for further ideas, ideally incorporating drones or agriculture design elements into the design of the business name. The business name needs work on the graphic/design – it is a draft that I have included, the drone propellers (being a different colour) are DRAFT only and intended for changes. PLEASE DO NOT USE THE DRONE PORPELLER I HAVE USED AS A DRAFT. TRY TO FIND SOMETHING ELSE.. The arrow is a shape and not aligned in any way, I would also like ideas on different fonts and additional elements, like air streams, aviation elements, aviation or country western (farming like) themes and fonts etc.
Ideally looking at staying within the blue, green and yellow colours, keeping with an natural, outdoorsy, environmental feel.

Target Market(s)

Farmers, Agriculture, Local Governments, Land Managers

Industry/Entity Type

Agriculture, Drones, Aviation

Contact Information for Business Card

Agricultural Drone (Voskel Ferra Q80), Farming, Business Name.

Font styles to use
Sans Serif

Colors
0054AA
0677BA
7BADD7
CADEEF
E8F1F8
0094D4
00A9DD
6FCCEA
C7EBF8
E9F6FB
00AB8E
00BBA5
67D7C9
C6EFE9
E9F9F6
59FF00
82FF00
B8FF75
E3FFCB
F4FFEA

Requirements
Must have
• Voskel Ferra Q80 Drone
Should not have
• Tractors

```html
<!DOCTYPE html>
<html lang="en">
<head>
<meta charset="utf-8">
<title>Larkmoor Drones Business Card</title>
<link rel="stylesheet" href="https://fonts.googleapis.com/css2?family=Cinzel:wght@700&family=Montserrat:ital,wght@0,600;0,700;0,800;1,800&display=swap">
<style>
  :root {
    --backdrop: #ececec;
    --card: #ffffff;
    --slate: #4b5c77;
    --olive: #7f8c3a;
    --ink: #1d1d1d;
    --white: #ffffff;
    --photo-top: #e9ecef;
    --photo-bottom: #9aa1a8;
  }
  * { margin: 0; padding: 0; box-sizing: border-box; }
  html, body {
    width: 1200px; height: 1199px; overflow: hidden;
    background: var(--backdrop);
    font-family: "Montserrat", Arial, sans-serif;
  }
  .card {
    position: absolute; left: 254px; width: 692px; height: 396px;
    background: var(--card); overflow: hidden;
  }
  .card--front { top: 188px; }
  .card--back { top: 624px; }

  .brand {
    position: absolute; left: 0; right: 0; top: 118px;
    text-align: center; color: var(--slate);
  }
  .brand__name {
    font-weight: 800; font-size: 46px; line-height: 52px; letter-spacing: 1px;
  }
  .brand__tagline {
    margin-top: 10px; font-family: "Cinzel", Georgia, serif; font-weight: 700;
    font-size: 15px; letter-spacing: 1px; color: var(--ink);
  }

  .wave { position: absolute; inset: 0; width: 692px; height: 396px; }

  .person { position: absolute; left: 32px; top: 50px; }
  .person__name {
    font-weight: 800; font-style: italic; font-size: 29px; line-height: 32px;
    color: var(--olive);
  }
  .person__role {
    font-weight: 700; font-size: 17px; color: var(--slate); margin-top: 2px; padding-left: 3px;
  }

  .drone-photo {
    position: absolute; left: 336px; top: 108px; width: 308px; height: 108px;
    background: linear-gradient(180deg, var(--photo-top), var(--photo-bottom));
    border-radius: 6px;
  }

  .contact {
    position: absolute; left: 28px; top: 220px; list-style: none;
    color: var(--white); font-weight: 600; font-size: 17px; line-height: 24px;
  }
  .contact__item { display: flex; align-items: flex-start; gap: 8px; margin-bottom: 4px; }
  .contact__item--address { align-items: flex-end; }
  .contact__icon { width: 17px; height: 17px; flex: none; margin-top: 3px; fill: var(--white); }
  .contact__item--address .contact__icon { margin-bottom: 26px; }
</style>
</head>
<body>

<section class="card card--front">
  <div class="brand">
    <div class="brand__name">LARKMOOR<br>DRONES</div>
    <div class="brand__tagline">Servicing Central Queensland</div>
  </div>
</section>

<section class="card card--back">
  <svg class="wave" viewBox="0 0 692 396" aria-hidden="true">
    <path fill="var(--olive)" d="M0,204 C40,170 95,152 155,158 C235,166 285,222 345,262 C410,304 480,326 580,330 L692,324 L692,396 L0,396 Z"/>
    <path fill="var(--white)" d="M335,256 C420,312 540,318 692,292 L692,324 L580,330 C480,326 410,304 345,262 Z"/>
    <path fill="var(--slate)" d="M340,258 C440,296 560,292 692,266 L692,296 C560,318 430,312 340,258 Z"/>
  </svg>

  <div class="person">
    <div class="person__name">SAM CARTER</div>
    <div class="person__role">CEO &amp; FOUNDER</div>
  </div>

  <div class="drone-photo" role="img" aria-label="Photo of a Voskel Ferra Q80 agricultural spray drone in flight"></div>

  <ul class="contact">
    <li class="contact__item">
      <svg class="contact__icon" viewBox="0 0 24 24"><path d="M6.6 10.8a15.1 15.1 0 0 0 6.6 6.6l2.2-2.2c.3-.3.7-.4 1-.2 1.1.4 2.3.6 3.6.6.6 0 1 .4 1 1V20c0 .6-.4 1-1 1A17 17 0 0 1 3 4c0-.6.4-1 1-1h3.5c.6 0 1 .4 1 1 0 1.3.2 2.5.6 3.6.1.3 0 .7-.2 1z"/></svg>
      <span>+61 7 4982 5316</span>
    </li>
    <li class="contact__item">
      <svg class="contact__icon" viewBox="0 0 24 24"><path d="M12 2a10 10 0 1 0 0 20 10 10 0 0 0 0-20zm6.9 6h-2.9a15.7 15.7 0 0 0-1.4-3.6A8 8 0 0 1 18.9 8zM12 4c.8 1.2 1.5 2.5 1.9 4h-3.8c.4-1.4 1.1-2.8 1.9-4zM4.3 14a8.2 8.2 0 0 1 0-4h3.4a16.5 16.5 0 0 0 0 4zm.8 2h2.9c.3 1.3.8 2.5 1.4 3.6A8 8 0 0 1 5.1 16zM8 8H5.1a8 8 0 0 1 4.3-3.6C8.8 5.5 8.3 6.7 8 8zm4 12c-.8-1.2-1.5-2.5-1.9-4h3.8c-.4 1.4-1.1 2.8-1.9 4zm2.3-6H9.7a14.7 14.7 0 0 1 0-4h4.6a14.7 14.7 0 0 1 0 4zm.3 5.6c.6-1.1 1.1-2.3 1.4-3.6h2.9a8 8 0 0 1-4.3 3.6zm1.7-5.6a16.5 16.5 0 0 0 0-4h3.4a8.2 8.2 0 0 1 0 4z"/></svg>
      <span>LARKMOORDRONES.COM</span>
    </li>
    <li class="contact__item">
      <svg class="contact__icon" viewBox="0 0 24 24"><path d="M3 5h18c.6 0 1 .4 1 1v.4l-10 6.2L2 6.4V6c0-.6.4-1 1-1zm-1 3.7 10 6.2 10-6.2V18c0 .6-.4 1-1 1H3c-.6 0-1-.4-1-1z"/></svg>
      <span>SAM.CARTER@LARKMOOR.COM</span>
    </li>
    <li class="contact__item contact__item--address">
      <svg class="contact__icon" viewBox="0 0 24 24"><path d="M12 2a7 7 0 0 0-7 7c0 5.2 7 13 7 13s7-7.8 7-13a7 7 0 0 0-7-7zm0 9.5a2.5 2.5 0 1 1 0-5 2.5 2.5 0 0 1 0 5z"/></svg>
      <span>18 DAWSON ROAD,<br>UNIT 4, EMERALD,<br>QLD 4720</span>
    </li>
  </ul>
</section>

</body>
</html>
```